TA BRAMLEY BUSINESS CARD DESIGN PROJECT

We need to utilize our logo that was expertly created on PixelHarbor and now need to match this with a business card design.

```html
<!DOCTYPE html>
<html lang="en">
<head>
<meta charset="utf-8">
<title>TA Bramley Business Card</title>
<link href="https://fonts.googleapis.com/css2?family=Montserrat:ital,wght@0,400;0,600;0,700;0,800;1,400&display=swap" rel="stylesheet">
<style>
  :root {
    --brand-blue: #0b55a8;
    --deep-blue: #0a4a94;
    --pattern-blue: #1a5fb0;
    --card-white: #ffffff;
    --backdrop: #1c1c1e;
  }
  html, body {
    margin: 0;
    padding: 0;
    width: 1200px;
    height: 884px;
    overflow: hidden;
    background: var(--backdrop);
    font-family: "Montserrat", sans-serif;
  }
  .canvas {
    position: relative;
    width: 1200px;
    height: 884px;
  }
  .card {
    position: absolute;
    top: 292px;
    width: 520px;
    height: 300px;
    border-radius: 18px;
    overflow: hidden;
  }
  .card-front { left: 50px; background: var(--card-white); }
  .card-back { left: 630px; background: var(--brand-blue); }

  .front-wave { position: absolute; inset: 0; }

  .brand-name {
    position: absolute;
    left: 36px;
    top: 36px;
    margin: 0;
    font-weight: 800;
    font-size: 34px;
    line-height: 40px;
    letter-spacing: 4px;
    color: var(--brand-blue);
  }
  .holder {
    position: absolute;
    right: 30px;
    top: 86px;
    text-align: right;
    color: var(--brand-blue);
  }
  .holder-name {
    margin: 0;
    font-weight: 700;
    font-size: 18px;
    line-height: 22px;
    letter-spacing: 1px;
  }
  .holder-title {
    margin: 1px 0 0;
    font-style: italic;
    font-size: 12px;
    line-height: 16px;
  }
  .contact {
    position: absolute;
    right: 30px;
    bottom: 18px;
    margin: 0;
    padding: 0;
    list-style: none;
    text-align: right;
    color: var(--card-white);
    font-size: 12px;
    line-height: 17px;
  }
  .contact li { display: flex; justify-content: flex-end; align-items: center; gap: 7px; }
  .contact .address { padding-right: 18px; }
  .contact svg { width: 11px; height: 11px; flex: none; }
  .icon-fill { fill: var(--card-white); }
  .icon-line { fill: none; stroke: var(--card-white); stroke-width: 2.5; }

  .back-pattern {
    position: absolute;
    inset: 0;
    background: linear-gradient(135deg, var(--deep-blue), var(--pattern-blue) 55%, var(--brand-blue));
  }
  .back-brand {
    position: absolute;
    right: 30px;
    bottom: 26px;
    margin: 0;
    font-weight: 800;
    font-size: 22px;
    letter-spacing: 2px;
    color: var(--card-white);
  }
</style>
</head>
<body>
<main class="canvas">
  <section class="card card-front" aria-label="Business card front">
    <svg class="front-wave" viewBox="0 0 520 300" aria-hidden="true">
      <path d="M0 108 C110 178 250 148 370 158 C450 165 500 158 520 138 L520 300 L0 300 Z" fill="var(--brand-blue)"/>
      <path d="M0 98 C110 168 250 138 370 148 C450 155 500 148 520 128" fill="none" stroke="var(--brand-blue)" stroke-width="2"/>
      <path d="M0 118 C110 188 250 158 370 168 C450 175 500 168 520 148" fill="none" stroke="var(--card-white)" stroke-width="2.5"/>
      <path d="M0 126 C110 196 250 166 370 176 C450 183 500 176 520 156" fill="none" stroke="var(--card-white)" stroke-width="1.5"/>
    </svg>
    <h1 class="brand-name">TA BRAMLEY</h1>
    <div class="holder">
      <p class="holder-name">DALE EVERTON</p>
      <p class="holder-title">President</p>
    </div>
    <ul class="contact">
      <li class="address">4150 Marlow Bay Rd</li>
      <li class="address">Cedar Cove CA 90410</li>
      <li>555-014-2290
        <svg viewBox="0 0 24 24"><path class="icon-fill" d="M6.6 10.8a15 15 0 0 0 6.6 6.6l2.2-2.2c.3-.3.7-.4 1-.2 1.1.4 2.3.6 3.6.6.6 0 1 .4 1 1V20c0 .6-.4 1-1 1A17 17 0 0 1 3 4c0-.6.4-1 1-1h3.5c.6 0 1 .4 1 1 0 1.3.2 2.5.6 3.6.1.3 0 .7-.2 1z"/></svg>
      </li>
      <li>d.everton@tabramley.com
        <svg viewBox="0 0 24 24"><path class="icon-line" d="M3 6h18v12H3z M3 6l9 7 9-7"/></svg>
      </li>
      <li>www.tabramley.com
        <svg viewBox="0 0 24 24"><circle class="icon-line" cx="12" cy="12" r="9"/><path class="icon-line" d="M3 12h18 M12 3c4 4 4 14 0 18 M12 3c-4 4-4 14 0 18"/></svg>
      </li>
    </ul>
  </section>

  <section class="card card-back" aria-label="Business card back">
    <div class="back-pattern" role="img" aria-label="Repeating brand mark pattern in tonal blues"></div>
    <p class="back-brand">TA BRAMLEY</p>
  </section>
</main>
</body>
</html>
```